Redesign This Psychology Website

We would like a slight redesign of this successful psychology (relationship counselling) website:

www.TheKelvaleClinic.com.au

We are updating the website, and we'd like a slight refresh of the design and style.

Please keep to very similar colours, and use the same logo. We're looking for around 10 page templates, however the main one is the home page.

Keep in mind, this website already converts quite well, so we want a new, fresh design in keeping with this one. Please don't bother designing something too extremely different.

thanks :)

Target Market(s)

couples who are looking for relationship counselling. Men and women, 25 - 70, across Australia

Industry/Entity Type

Psychology

Number of Pages Required

5+ page

Font styles to use
Sans Serif

Colors
87cfc6
b7a5cd
ec1f27
ffffff
cee9f5

Requirements
Must have
• a similar look to the current design, just looking for a slight refresh.
• Search bar
• Areas for lots of photos
• same logo
• lots of content areas
Nice to have
• great content areas, where we can display a lot of content and our areas.
Should not have
• no colors like orange, etc.
• should not have a totally different feel.

```html
<!DOCTYPE html>
<html lang="en">
<head>
<meta charset="utf-8">
<title>The Kelvale Clinic – Relationship &amp; Marriage Counselling</title>
<link href="https://fonts.googleapis.com/css2?family=Open+Sans:wght@300;400;600;700&display=swap" rel="stylesheet">
<style>
:root{
  --teal:#87cfc6;
  --teal-dark:#5fb8ad;
  --purple:#b7a5cd;
  --purple-dark:#9a85b8;
  --red:#ec1f27;
  --sky:#cee9f5;
  --white:#ffffff;
  --ink:#3a3a3a;
  --grey:#7d7d7d;
  --light:#f2f2f2;
  --line:#e1e1e1;
}
*{box-sizing:border-box;margin:0;padding:0}
html,body{width:1200px;height:4478px;overflow:hidden}
body{font-family:"Open Sans",Arial,sans-serif;color:var(--ink);background:var(--white);font-size:14px}
.wrap{width:940px;margin:0 auto;position:relative}
a{color:inherit;text-decoration:none}
.photo{display:block}

/* top bar */
.topbar{height:36px;background:var(--light);border-bottom:1px solid var(--line)}
.topbar .wrap{display:flex;justify-content:space-between;align-items:center;height:36px;font-size:12px;color:#666}
.topbar nav{display:flex}
.topbar nav a{padding:0 12px;border-left:1px solid #ccc}
.topbar nav a:first-child{border-left:0}

/* header */
.header{height:129px}
.header .wrap{display:flex;align-items:center;height:129px}
.brand{display:flex;align-items:center;gap:12px;width:338px}
.brand-dot{width:46px;height:46px;border-radius:50%;background:var(--red)}
.brand-name{font-size:25px;font-weight:600;color:#555;line-height:1}
.brand-tag{font-size:11px;color:var(--teal-dark);margin-top:5px}
.search{width:352px;height:38px;border:1px solid #d6d6d6;border-radius:3px;display:flex;align-items:center;padding:0 12px;gap:8px;color:#999;font-size:13px}
.call{margin-left:auto;text-align:right}
.call small{display:block;color:var(--teal-dark);font-size:14px}
.call strong{font-size:26px;color:var(--red);font-weight:600;display:flex;align-items:center;gap:8px}

/* nav */
.mainnav{height:65px;background:var(--teal)}
.mainnav ul{list-style:none;display:flex;height:65px;width:940px;margin:0 auto}
.mainnav li{display:flex;align-items:center;padding:0 12px;color:var(--white);font-size:14px;font-weight:600;line-height:1.2;border-right:1px solid rgba(255,255,255,.45)}
.mainnav li:last-child{border-right:0}
.mainnav li.active{background:var(--teal-dark)}

/* hero */
.hero{height:510px;position:relative;background:linear-gradient(110deg,#6f8a4c 0%,#b8b07a 35%,#e7d9b9 60%,#c7b48b 100%)}
.hero-title{position:absolute;left:130px;top:262px;color:var(--white);font-size:38px;font-weight:600;line-height:1.3;text-transform:uppercase}
.finder{position:absolute;left:770px;top:90px;width:290px;height:340px;background:rgba(183,165,205,.92);padding:22px 26px}
.finder h2{color:var(--white);font-size:21px;font-weight:600;text-align:center;line-height:1.3;margin-bottom:14px}
.finder label{display:block;color:var(--white);font-size:12px;margin:8px 0 4px}
.field{height:30px;background:var(--white);font-size:12px;color:#888;display:flex;align-items:center;justify-content:space-between;padding:0 10px}
.finder .btn-search{margin-top:16px;height:34px;background:var(--red);color:var(--white);font-weight:600;display:flex;align-items:center;justify-content:center;letter-spacing:1px}
.dots{position:absolute;left:560px;top:700px;display:flex;gap:8px}
.hero .dots{top:468px}
.dots i{width:10px;height:10px;border-radius:50%;background:rgba(255,255,255,.6)}
.dots i.on{background:var(--white)}

/* intro */
.intro{height:385px;position:relative}
.intro .wrap{display:flex;gap:46px;padding-top:50px}
.video{width:436px;height:270px;position:relative;border:4px solid #eee;background:linear-gradient(135deg,#b9c3c8,#8f9ea5 60%,#d7c9bd)}
.video svg.play{position:absolute;left:183px;top:100px}
.intro h2{font-size:29px;font-weight:600;line-height:1.25;color:#333;margin-top:0}
.intro p{margin-top:18px;font-size:15px;line-height:1.7;color:var(--grey)}
.divider{position:absolute;left:130px;bottom:0;width:940px;height:1px;background:var(--line)}
.divider::after{content:"";position:absolute;left:455px;top:-1px;border:12px solid transparent;border-top-color:var(--line)}

/* services */
.services{height:421px}
.services .wrap{display:flex;gap:9px;padding-top:45px}
.card{width:228px;height:338px;border:1px solid var(--line)}
.card .photo{height:165px}
.card-body{padding:14px 16px}
.card h3{font-size:18px;font-weight:600;line-height:1.2}
.card p{font-size:11px;line-height:1.5;color:var(--grey);margin:8px 0 12px;min-height:50px}
.btn{display:inline-block;padding:7px 16px;color:var(--white);font-size:12px;font-weight:600;border-radius:2px}
.purple{color:var(--purple-dark)}.red{color:var(--red)}.teal{color:var(--teal-dark)}
.bg-purple{background:var(--purple)}.bg-red{background:var(--red)}.bg-teal{background:var(--teal)}

/* psychologists band */
.psych{height:469px;position:relative;overflow:hidden;background:linear-gradient(160deg,var(--purple) 0%,#a7aacb 55%,var(--teal) 100%)}
.psych .photo{position:absolute;inset:0;width:1200px;height:469px}
.psych-text{position:absolute;left:130px;top:68px;color:var(--white);width:560px}
.psych-text h2{font-size:32px;font-weight:300}
.psych-text .lead{font-size:17px;margin:6px 0 22px}
.psych-text ul{list-style:none;columns:2;column-gap:20px;font-size:14px}
.psych-text li{margin-bottom:14px;padding-left:16px;position:relative}
.psych-text li::before{content:"›";position:absolute;left:0;top:-2px;font-size:16px}

/* topics */
.topics{height:525px}
.topics .wrap{display:grid;grid-template-columns:463px 463px;gap:20px 14px;padding-top:51px}
.topic{height:212px;border:1px solid var(--line);display:flex;overflow:hidden}
.topic-text{width:231px;padding:24px 26px}
.topic h3{font-size:21px;font-weight:400;color:#333;line-height:1.2}
.topic p{font-size:12px;line-height:1.5;color:var(--grey);margin:8px 0 6px}
.topic a{font-size:11px;color:var(--teal-dark);font-weight:600}
.topic .photo{width:231px;height:212px}

/* insights */
.insights{height:370px}
.insights .wrap{display:flex;gap:40px;padding-top:42px}
.col{width:287px}
.col h3{font-size:20px;font-weight:400;line-height:1.3;min-height:52px}
.col p{font-size:12px;line-height:1.8;color:var(--grey);margin:14px 0 18px;min-height:140px}
.col .locs{display:grid;grid-template-columns:1fr 1fr;font-size:12px;line-height:1.8;color:#555;margin:-4px 0 22px;min-height:94px}
.col .btn{width:124px;text-align:center}

/* stories */
.stories{height:344px;background:#ededed;position:relative}
.stories .wrap{display:flex;gap:17px;padding-top:60px}
.story{width:291px;height:224px}
.story .photo{height:164px}
.story span{display:flex;height:60px;align-items:center;justify-content:center;background:var(--purple);color:var(--white);font-size:17px}
.bars{position:absolute;left:530px;top:318px;display:flex;gap:8px}
.bars i{width:26px;height:4px;background:#9a9a9a}
.bars i.on{background:#e58c7e}

/* blogs */
.blogs{height:859px}
.blogs h2{font-size:34px;font-weight:400;color:var(--red);padding-top:42px}
.blog-grid{display:flex;gap:9px;margin-top:22px}
.post{width:228px}
.post .thumb{position:relative;height:141px}
.post .thumb .photo{height:141px}
.date{position:absolute;left:0;bottom:0;width:44px;height:50px;background:var(--teal);color:var(--white);text-align:center;font-size:20px;font-weight:600;line-height:1;padding-top:8px}
.date small{display:block;font-size:9px;font-weight:400;margin-top:3px}
.post h3{font-size:14px;font-weight:600;margin:12px 0 6px}
.post p{font-size:10px;line-height:1.5;color:var(--grey)}
.post a{display:block;font-size:11px;color:var(--teal-dark);margin-top:8px}
.mini-grid{display:grid;grid-template-columns:repeat(3,300px);gap:15px 20px;margin-top:24px}
.mini{height:114px;display:flex;gap:14px;align-items:flex-start;border:1px solid var(--line)}
.mini .photo{width:150px;height:112px;flex:none}
.mini h4{font-size:13px;font-weight:600;line-height:1.35;margin-top:12px}
.mini a{display:block;font-size:11px;color:var(--teal-dark);margin-top:5px}

/* footer */
.footer{height:290px;background:#f4f4f4}
.footer .wrap{display:flex;padding-top:75px}
.footer .brand{width:322px}
.fcol{width:168px}
.fcol h4{color:var(--teal-dark);font-size:14px;font-weight:700;text-transform:uppercase;margin-bottom:10px}
.fcol li{list-style:none;font-size:12px;line-height:1.9;color:#555}
.fcontact{width:250px}
.socials{display:flex;gap:6px;margin-top:10px}
.socials i{width:26px;height:26px;border-radius:50%;background:var(--teal-dark)}
.socials i:nth-child(4){background:var(--red)}
.copy{height:75px;display:flex;align-items:center;justify-content:center;font-size:12px;color:#777;background:var(--white)}
</style>
</head>
<body>

<header>
  <div class="topbar">
    <div class="wrap">
      <a href="#">Join Our Associate Program →</a>
      <nav><a href="#">Home</a><a href="#">Cart</a><a href="#">Blog</a><a href="#">Resources</a><a href="#">Contact</a></nav>
    </div>
  </div>
  <div class="header">
    <div class="wrap">
      <div class="brand">
        <span class="brand-dot"></span>
        <div><div class="brand-name">The Kelvale Clinic</div><div class="brand-tag">helping you create loving relationships</div></div>
      </div>
      <div class="search">
        <svg width="14" height="14" viewBox="0 0 14 14"><circle cx="6" cy="6" r="4.5" fill="none" stroke="#999" stroke-width="1.5"/><line x1="9.5" y1="9.5" x2="13" y2="13" stroke="#999" stroke-width="1.5"/></svg>
        Search here
      </div>
      <div class="call">
        <small>Call Us Now</small>
        <strong><svg width="22" height="22" viewBox="0 0 24 24"><path d="M6.6 10.8a15 15 0 0 0 6.6 6.6l2.2-2.2c.3-.3.7-.4 1-.2 1.1.4 2.3.6 3.6.6.6 0 1 .4 1 1V20c0 .6-.4 1-1 1A17 17 0 0 1 3 4c0-.6.4-1 1-1h3.5c.6 0 1 .4 1 1 0 1.3.2 2.5.6 3.6.1.3 0 .7-.2 1z" fill="#ec1f27"/></svg>1300 555 014</strong>
      </div>
    </div>
  </div>
  <nav class="mainnav">
    <ul>
      <li>COUNSELLING<br>TYPES</li>
      <li>RELATIONSHIP COUNSELLING<br>LOCATIONS</li>
      <li class="active">SEX THERAPY<br>LOCATIONS</li>
      <li>ABOUT US</li>
      <li>QUIZZES</li>
      <li>FAQ'S</li>
      <li>CONTACT</li>
    </ul>
  </nav>
</header>

<main>
  <section class="hero" role="img" aria-label="Photo of a happy couple laughing outdoors">
    <h1 class="hero-title">Relationship &amp;<br>Marriage Counselling</h1>
    <form class="finder">
      <h2>Find Our Psychologist Near You</h2>
      <label>Type of Counselling</label>
      <div class="field">Select <span>▾</span></div>
      <label>Location</label>
      <div class="field"></div>
      <label>Postcode</label>
      <div class="field"></div>
      <div class="btn-search">SEARCH</div>
    </form>
    <div class="dots"><i class="on"></i><i></i><i></i><i></i></div>
  </section>

  <section class="intro">
    <div class="wrap">
      <div class="video" role="img" aria-label="Video still of a psychologist speaking to camera">
        <svg class="play" width="62" height="62" viewBox="0 0 62 62"><circle cx="31" cy="31" r="28" fill="rgba(255,255,255,.25)" stroke="#fff" stroke-width="3"/><path d="M25 19l18 12-18 12z" fill="#fff"/></svg>
      </div>
      <div>
        <h2>We Specialise in Relationship<br>&amp; Marriage Counselling</h2>
        <p>At the Kelvale Clinic, we are a group of PSYCHOLOGISTS, Australia wide who are passionate about relationships and helping you with yours. Our vision is to provide the most highly regarded and comprehensive marriage counselling and relationship counselling, and sex therapy in Australia, at reasonable and affordable rates.</p>
      </div>
    </div>
    <span class="divider"></span>
  </section>

  <section class="services">
    <div class="wrap">
      <article class="card">
        <div class="photo" role="img" aria-label="Photo of a couple in a counselling session" style="background:linear-gradient(135deg,#d9cfc4,#a89a8c)"></div>
        <div class="card-body"><h3 class="purple">Relationship Counselling</h3><p>Communication, Recovering from an affair, Loss of intimacy &amp; love, Power battles, Fighting.</p><a class="btn bg-purple">Learn More</a></div>
      </article>
      <article class="card">
        <div class="photo" role="img" aria-label="Photo of a couple in bed" style="background:linear-gradient(135deg,#f0e4e6,#d9a9b2)"></div>
        <div class="card-body"><h3 class="red">Sex Therapy Counselling</h3><p>Low libido, Erectile difficulties, Premature ejaculation, Differing libidos, Porn addiction.</p><a class="btn bg-red">Learn More</a></div>
      </article>
      <article class="card">
        <div class="photo" role="img" aria-label="Photo of a couple arguing" style="background:linear-gradient(135deg,#8e7f70,#4d463f)"></div>
        <div class="card-body"><h3 class="teal">Anger Management Counselling</h3><p>Managing angry outbursts, expressing your anger in healthy ways.</p><a class="btn bg-teal">Learn More</a></div>
      </article>
      <article class="card">
        <div class="photo" role="img" aria-label="Photo of a tense couple" style="background:linear-gradient(135deg,#6a5a50,#2f2925)"></div>
        <div class="card-body"><h3 class="teal">Narcissism Counselling</h3><p>Managing narcissistic, suspicious, entitled, arrogant and lack of empathy tendencies.</p><a class="btn bg-teal">Learn More</a></div>
      </article>
    </div>
  </section>

  <section class="psych">
    <svg class="photo" viewBox="0 0 1200 469" role="img" aria-label="Photo of a smiling mature couple by the sea">
      <defs><linearGradient id="psychPhoto" x1="0" y1="0" x2="1" y2="1"><stop offset="0" stop-color="#d8dfe4"/><stop offset=".5" stop-color="#b7a394"/><stop offset="1" stop-color="#8b7766"/></linearGradient></defs>
      <polygon points="780,0 1200,0 1200,469 600,469" fill="url(#psychPhoto)"/>
      <polygon points="780,0 800,0 630,469 600,469" fill="#87cfc6"/>
    </svg>
    <div class="psych-text">
      <h2>Our Kelvale Relationship Psychologists</h2>
      <p class="lead">Here are some of the common ones:</p>
      <ul>
        <li>Affairs</li><li>Controlling behaviour</li><li>Verbal abuse</li><li>Imbalance of power</li><li>Lack of intimacy</li><li>Poor communication</li><li>Loss of love</li>
        <li>Relationship neglect</li><li>Sexual problems</li><li>Problems from childhood</li><li>Problems with parenting your children</li><li>Step children and in-laws</li><li>All forms of family problems</li><li>Anger management problems</li>
      </ul>
    </div>
  </section>

  <section class="topics">
    <div class="wrap">
      <article class="topic">
        <div class="topic-text"><h3>Anxiety</h3><p>Learn calm ways to ease worry and restore balance in daily life together.</p><a>READ MORE</a></div>
        <div class="photo" role="img" aria-label="Photo of an anxious woman" style="background:linear-gradient(135deg,#5b5e62,#1f2124)"></div>
      </article>
      <article class="topic">
        <div class="photo" role="img" aria-label="Photo of a woman holding her head" style="background:linear-gradient(135deg,#c9b6a6,#7d6a5c)"></div>
        <div class="topic-text"><h3>GP referral info</h3><p>Find out how a GP plan can help reduce the cost of your sessions.</p><a>READ MORE</a></div>
      </article>
      <article class="topic">
        <div class="topic-text"><h3>Depression</h3><p>Support to lift low mood and reconnect with the people you love most.</p><a>READ MORE</a></div>
        <div class="photo" role="img" aria-label="Photo of a sad woman" style="background:linear-gradient(135deg,#b9aaa0,#6a5c55)"></div>
      </article>
      <article class="topic">
        <div class="photo" role="img" aria-label="Illustration of two trees reaching toward each other" style="background:linear-gradient(135deg,#e3e8df,#98a98d)"></div>
        <div class="topic-text"><h3>Sex Therapy Locations</h3><p>See where our sex therapists practise near you today.</p><a>READ MORE</a></div>
      </article>
    </div>
  </section>

  <section class="insights">
    <div class="wrap">
      <div class="col">
        <h3 class="red">Communication is a vital skill but not often taught to us.</h3>
        <p>Most people find that their ways of communicating with each other are what hamper us from having a happy healthy relationship. Effective interpersonal communication skills are not something that we are usually taught. But for almost everyone who is having difficulties.</p>
        <a class="btn bg-red">Learn More</a>
      </div>
      <div class="col">
        <h3 class="teal">We as individuals have specific patterns in our relationships.</h3>
        <p>We can also assist you if you want individual help and guidance on your relationship, so you can learn what the patterns in your relationships are showing you about yourself. If you have been in a number of relationships and have found yourself repeating the same kind of experiences.</p>
        <a class="btn bg-teal">Learn More</a>
      </div>
      <div class="col">
        <h3 class="purple">Our Relationship Counselling Locations across Australia</h3>
        <p style="min-height:0;margin-bottom:10px">We currently have relationship counselling and marriage counselling services in:</p>
        <div class="locs">
          <span>Sydney – 19 centres</span><span>Brisbane – 14 centres</span>
          <span>Canberra – 2 centres</span><span>Newcastle – 1 centre</span>
          <span>Melbourne – 21 centres</span><span>Central Coast – 2 centres</span>
          <span>Perth – 11 centres</span><span>Adelaide – 4 centres</span>
        </div>
        <a class="btn bg-purple">Learn More</a>
      </div>
    </div>
  </section>

  <section class="stories">
    <div class="wrap">
      <article class="story"><div class="photo" role="img" aria-label="Photo of an upset woman" style="background:linear-gradient(135deg,#a99b91,#5e534c)"></div><span>How to Deal with an Affair?</span></article>
      <article class="story"><div class="photo" role="img" aria-label="Photo of two men together" style="background:linear-gradient(135deg,#9d8774,#3f342c)"></div><span>Same Sex Relationship</span></article>
      <article class="story"><div class="photo" role="img" aria-label="Photo of a couple in conflict" style="background:linear-gradient(135deg,#8a7b70,#3b332e)"></div><span>Are You living with a narcissist?</span></article>
    </div>
    <div class="bars"><i></i><i></i><i class="on"></i><i></i></div>
  </section>

  <section class="blogs">
    <div class="wrap">
      <h2>Latest Blogs</h2>
      <div class="blog-grid">
        <article class="post"><div class="thumb"><div class="photo" role="img" aria-label="Photo of a couple apart" style="background:linear-gradient(135deg,#e8dcd4,#b89d8e)"></div><div class="date">15<small>APR</small></div></div><h3>Your Blog Title here</h3><p>Short notes on building trust, honest talk and shared time as a couple.</p><a>Read More</a></article>
        <article class="post"><div class="thumb"><div class="photo" role="img" aria-label="Photo of a couple talking" style="background:linear-gradient(135deg,#7b6a5e,#3a302a)"></div><div class="date">18<small>APR</small></div></div><h3>Your Blog Title here</h3><p>Short notes on building trust, honest talk and shared time as a couple.</p><a>Read More</a></article>
        <article class="post"><div class="thumb"><div class="photo" role="img" aria-label="Photo of a couple sitting back to back" style="background:linear-gradient(135deg,#6f6660,#2f2a27)"></div><div class="date">16<small>APR</small></div></div><h3>Your Blog Title here</h3><p>Short notes on building trust, honest talk and shared time as a couple.</p><a>Read More</a></article>
        <article class="post"><div class="thumb"><div class="photo" role="img" aria-label="Photo of a couple silhouetted at sunset" style="background:linear-gradient(180deg,#f6b35a,#d9642c 70%,#5a2a18)"></div><div class="date">05<small>APR</small></div></div><h3>Your Blog Title here</h3><p>Short notes on building trust, honest talk and shared time as a couple.</p><a>Read More</a></article>
      </div>
      <div class="mini-grid">
        <article class="mini"><div class="photo" role="img" aria-label="Photo of a couple in discussion" style="background:linear-gradient(135deg,#8c7c70,#3e3631)"></div><div><h4>What can I do if I'm living with a Narcissist?</h4><a>Read More</a></div></article>
        <article class="mini"><div class="photo" role="img" aria-label="Photo of a frustrated couple" style="background:linear-gradient(135deg,#b8a79a,#6a5a4f)"></div><div><h4>Why am I with a Narcissist?</h4><a>Read More</a></div></article>
        <article class="mini"><div class="photo" role="img" aria-label="Photo of a woman looking worried" style="background:linear-gradient(135deg,#9a8a80,#4a3f38)"></div><div><h4>How Do I Know If I'm With a Narcissist?</h4><a>Read More</a></div></article>
        <article class="mini"><div class="photo" role="img" aria-label="Photo of a man shouting" style="background:linear-gradient(135deg,#7a6d64,#342d29)"></div><div><h4>Are You Living With a Steamroller?</h4><a>Read More</a></div></article>
        <article class="mini"><div class="photo" role="img" aria-label="Photo of a woman writing a letter" style="background:linear-gradient(135deg,#d3c6bb,#8c7a6d)"></div><div><h4>Letter for a Partner Doubtful About Relationship Counselling</h4><a>Read More</a></div></article>
        <article class="mini"><div class="photo" role="img" aria-label="Photo of a smiling couple" style="background:linear-gradient(135deg,#e3cdb8,#a3806a)"></div><div><h4>Do You Wonder Why You and Your Partner Are Together?</h4><a>Read More</a></div></article>
        <article class="mini"><div class="photo" role="img" aria-label="Photo of a couple at odds" style="background:linear-gradient(135deg,#8f8178,#403833)"></div><div><h4>Did Your Relationship Start on Rocky Ground?</h4><a>Read More</a></div></article>
        <article class="mini"><div class="photo" role="img" aria-label="Photo of a couple embracing" style="background:linear-gradient(135deg,#d8d1c2,#8f9a78)"></div><div><h4>What Are You Like in a Relationship?</h4><a>Read More</a></div></article>
        <article class="mini"><div class="photo" role="img" aria-label="Photo of a businessman at a desk" style="background:linear-gradient(135deg,#a3a7ab,#4c5156)"></div><div><h4>Is Your Pursuit of Success Sabotaging Your Relationships That Matter Most?</h4><a>Read More</a></div></article>
      </div>
    </div>
  </section>
</main>

<footer>
  <div class="footer">
    <div class="wrap">
      <div class="brand" style="align-items:flex-start">
        <span class="brand-dot"></span>
        <div><div class="brand-name">The Kelvale Clinic</div><div class="brand-tag">helping you create loving relationships</div></div>
      </div>
      <div class="fcol"><h4>Quick Links</h4><ul><li>Home</li><li>About Us</li><li>Our Blogs</li><li>Shop Cart</li><li>Contact Us</li></ul></div>
      <div class="fcol"><h4>Resources</h4><ul><li>Counselling Type</li><li>Sex Therapy</li><li>Quizzes</li><li>FAQ</li><li>Relationship Counselling</li></ul></div>
      <div class="fcol fcontact"><h4>Contact Us</h4><ul><li>42 Harbour Lane Suite 7</li><li>1300 555 014</li><li>Email: info@kelvaleclinic.com.au</li></ul><div class="socials"><i></i><i></i><i></i><i></i></div></div>
    </div>
  </div>
  <div class="copy">© 2017 Company Name. All right reserved</div>
</footer>

</body>
</html>
```